Financial Advisor Resource Firm needs business card design

Need business card design for company in Omaha NE called Meridale Circle. We provide resources to financial advisors....workshop programs, retirement analysis, and insurance planning. I would like to see designs that use grays, greens, black, and white colors. The final design should communicate 'collaboration' and be simple yet attractive to financial planning clients. I will attached our logo and another picture of a puzzle piece coming together. I would like the incorporate the puzzle picture somehow, maybe on the back somehow, with color or just the gray scale....OR, the picture be the front of the card with 'Meridale' definition on it (see upload) and then company logo, employee name, title, address on the back (see ppt uploaded). The following disclosure needs to be included somewhere- Advisory services offered through Stonebrook Assets, LLC.
Updates

I uploaded a svg and ai file of the logo

Target Market(s)

Financial planning clients and financial advisors....so pretty diverse age range of about 40-70.

Industry/Entity Type

Financial Planning

Contact Information for Business Card

Tobias L. Fenwright, MBA
Founder/President
5287 E. Larkin Road
Suite 230
Omaha, NE 68190
Phone- (402) 555-0147
Cell- (402) 555-0183
Fax- (402) 555-0129
email- tobias@meridaleplan.example
web address- www.meridaleplan.example

Colors
1b1b1b
474747
d3d3d3
ffffff
9bcb3c
abd036

Requirements
Must have
• Must include logo provided, must be 2 sided, and must have disclosure...all of these items listed in project description

```html
<!DOCTYPE html>
<html lang="en">
<head>
<meta charset="utf-8">
<title>Meridale Circle — Business Card</title>
<link href="https://fonts.googleapis.com/css2?family=Poppins:wght@300;400;600&display=swap" rel="stylesheet">
<style>
  :root {
    --card: #262626;
    --ink: #ffffff;
    --soft: #d3d3d3;
    --muted: #9a9a9a;
    --green: #9bcb3c;
    --stage: #ececec;
  }
  * { box-sizing: border-box; margin: 0; padding: 0; }
  html, body { width: 1200px; height: 800px; overflow: hidden; }
  body {
    background: var(--stage);
    font-family: "Poppins", sans-serif;
    display: flex;
    align-items: center;
    justify-content: center;
    gap: 120px;
  }
  .card {
    width: 360px;
    height: 630px;
    background: var(--card);
    color: var(--ink);
    position: relative;
    box-shadow: 0 10px 30px rgba(0,0,0,0.18);
  }
  .brand {
    display: flex;
    align-items: center;
    justify-content: center;
    gap: 10px;
  }
  .brand-dot {
    width: 14px; height: 14px;
    border-radius: 50%;
    background: var(--green);
  }
  .brand-name {
    font-weight: 400;
    font-size: 26px;
    letter-spacing: 1px;
    color: var(--ink);
  }
  /* Front */
  .card-front .brand { position: absolute; top: 88px; left: 0; right: 0; }
  .holder { position: absolute; top: 168px; left: 0; right: 0; text-align: center; }
  .holder-name {
    font-weight: 600; font-size: 19px; letter-spacing: 0.5px;
    color: var(--green); text-transform: uppercase;
  }
  .holder-title { font-weight: 300; font-size: 13px; color: var(--soft); margin-top: 2px; }
  .address {
    position: absolute; top: 232px; left: 0; right: 0;
    text-align: center; font-style: normal;
    font-weight: 300; font-size: 12px; line-height: 18px; color: var(--soft);
  }
  .contacts {
    position: absolute; top: 300px; left: 0; right: 0;
    list-style: none; text-align: center;
  }
  .contact { margin-bottom: 8px; }
  .contact-mark {
    display: flex; align-items: center; justify-content: center; gap: 10px;
    margin-bottom: 4px;
  }
  .contact-mark::before, .contact-mark::after {
    content: ""; width: 42px; height: 1px; background: var(--green);
  }
  .contact-icon { width: 18px; height: 18px; display: block; }
  .contact-text { font-weight: 300; font-size: 13.5px; letter-spacing: 0.6px; color: var(--ink); }
  .web .accent { color: var(--green); }
  /* Back */
  .card-back .brand { position: absolute; top: 225px; left: 0; right: 0; }
  .card-back .web {
    position: absolute; top: 420px; left: 50px;
    font-weight: 300; font-size: 14px; letter-spacing: 1.4px;
  }
  .disclosure {
    position: absolute; bottom: 36px; left: 30px; right: 30px;
    text-align: center; font-weight: 300; font-size: 10px;
    letter-spacing: 0.3px; color: var(--muted);
  }
</style>
</head>
<body>

<section class="card card-front" aria-label="Card front">
  <div class="brand">
    <span class="brand-dot"></span>
    <span class="brand-name">Meridale Circle</span>
  </div>

  <div class="holder">
    <p class="holder-name">Tobias L. Fenwright, MBA</p>
    <p class="holder-title">Founder / President</p>
  </div>

  <address class="address">
    5287 E. Larkin Road, Suite 230<br>
    Omaha, NE 68190
  </address>

  <ul class="contacts">
    <li class="contact">
      <div class="contact-mark">
        <svg class="contact-icon" viewBox="0 0 18 18" aria-hidden="true"><circle cx="9" cy="9" r="9" fill="#9bcb3c"/><path d="M6 5.2l1.6-.4.9 2-1 .8a5 5 0 0 0 2.3 2.3l.8-1 2 .9-.4 1.6c-3.3.3-6.5-2.9-6.2-6.2z" fill="#262626"/></svg>
      </div>
      <p class="contact-text">(402) 555-0147</p>
    </li>
    <li class="contact">
      <div class="contact-mark">
        <svg class="contact-icon" viewBox="0 0 18 18" aria-hidden="true"><circle cx="9" cy="9" r="9" fill="#9bcb3c"/><rect x="6.3" y="4.3" width="5.4" height="9.4" rx="0.9" fill="none" stroke="#262626" stroke-width="1.2"/><circle cx="9" cy="12.2" r="0.6" fill="#262626"/></svg>
      </div>
      <p class="contact-text">(402) 555-0183</p>
    </li>
    <li class="contact">
      <div class="contact-mark">
        <svg class="contact-icon" viewBox="0 0 18 18" aria-hidden="true"><circle cx="9" cy="9" r="9" fill="#9bcb3c"/><rect x="6.2" y="4.5" width="5.6" height="3" fill="#262626"/><rect x="4.5" y="7.5" width="9" height="4" rx="0.6" fill="#262626"/><rect x="6.2" y="10.5" width="5.6" height="3" fill="#ffffff" stroke="#262626" stroke-width="0.8"/></svg>
      </div>
      <p class="contact-text">(402) 555-0129</p>
    </li>
    <li class="contact">
      <div class="contact-mark">
        <svg class="contact-icon" viewBox="0 0 18 18" aria-hidden="true"><circle cx="9" cy="9" r="9" fill="#9bcb3c"/><rect x="4.5" y="5.8" width="9" height="6.4" fill="none" stroke="#262626" stroke-width="1.1"/><path d="M4.6 6l4.4 3.4L13.4 6" fill="none" stroke="#262626" stroke-width="1.1"/></svg>
      </div>
      <p class="contact-text">tobias@meridaleplan.example</p>
    </li>
    <li class="contact">
      <div class="contact-mark">
        <svg class="contact-icon" viewBox="0 0 18 18" aria-hidden="true"><circle cx="9" cy="9" r="9" fill="#9bcb3c"/><circle cx="9" cy="9" r="4.5" fill="none" stroke="#262626" stroke-width="1"/><ellipse cx="9" cy="9" rx="2" ry="4.5" fill="none" stroke="#262626" stroke-width="1"/><path d="M4.5 9h9" stroke="#262626" stroke-width="1"/></svg>
      </div>
      <p class="contact-text web">www.<span class="accent">meridaleplan</span>.example</p>
    </li>
  </ul>
</section>

<section class="card card-back" aria-label="Card back">
  <div class="brand">
    <span class="brand-dot"></span>
    <span class="brand-name">Meridale Circle</span>
  </div>
  <p class="web">www.<span class="accent">meridaleplan</span>.example</p>
  <p class="disclosure">Advisory services offered through Stonebrook Assets, LLC.</p>
</section>

</body>
</html>
```